Community Harvest Festival Poster

Seeking a poster design to advertise our community’s annual Harvest Festival. We will utilize and display printed posters as well as distribute PDFs via our weekly e-news letters. This years "theme" is, "Copper Kettle/Maple Lane Meadow, Where City and Country Meet." The vibe is a bohemian, beatnik, street scene, meets a old fashioned orchard.

Target Market(s)

NYC School Community- should appeal to an audience that ranges from kids to grandparents. Very family oriented, with wide appeal, and must be eye catching.

Other font styles liked:
• One style should be more of a "Country" font, the other should have more of a clean city vibe.

Colors
acd037
ffc214
f68e4e
eaf2ce

Requirements
Must have
• The following copy:
• Copper Kettle Maple Lane Meadow
• Where City and Country Meet
• Celebrate C&C With Great Food, Music, Entertainment, And Fun!
• Saturday, October 19th 2019
• 12:00-4:00pm
• Tickets will be available for sale at Drop off and Pick up
Nice to have
• I'm not limited, but a couple of ideas that could be cool:
• One incorporated the background of a street, i.e. pavement, which has leaves blowing over it, and perhaps an apple or two rolling onto the page.
• Another has a diagonal breakup of the image, with one side pavement and the other side rustic wood, also with leaves sweeping across.
• I've also attached images of previous festival posters that I have gravitated to for some idea of quality I'm looking for.
Should not have
• Anything inappropriate for children.

```html
<!DOCTYPE html>
<html lang="en">
<head>
<meta charset="utf-8">
<title>Harvest Festival – Copper Kettle Maple Lane Meadow</title>
<link rel="stylesheet" href="https://fonts.googleapis.com/css2?family=Fredoka:wght@600&family=Rye&family=Quicksand:wght@700&family=Titan+One&family=Open+Sans:ital,wght@1,700&display=swap">
<style>
  :root {
    --wood-light: #a27146;
    --wood-mid: #7e5431;
    --wood-dark: #5a391f;
    --leaf-gold: #ffc214;
    --leaf-orange: #f68e4e;
    --leaf-rust: #d2481c;
    --leaf-red: #b8261a;
    --date-ink: #ffffff;
    --date-edge: #6a22c4;
    --title-ink: #ffffff;
    --title-edge: #8a1a22;
    --tagline-ink: #ffff1a;
    --tagline-glow: #b3261a;
    --time-ink: #ffffff;
    --time-edge: #2740d8;
    --ticket-ink: #ffffff;
  }
  html, body {
    margin: 0;
    padding: 0;
    overflow: hidden;
    background: #ffffff;
  }
  .poster {
    position: relative;
    width: 847px;
    height: 1200px;
    overflow: hidden;
  }
  .poster svg { display: block; }
  .date-line {
    font-family: "Fredoka", sans-serif;
    font-weight: 600;
    fill: var(--date-ink);
    stroke: var(--date-edge);
    stroke-width: 3px;
    paint-order: stroke;
  }
  .title-word {
    font-family: "Rye", serif;
    fill: var(--title-ink);
    stroke: var(--title-edge);
    stroke-width: 2.5px;
    paint-order: stroke;
  }
  .title-frame {
    fill: none;
    stroke: var(--title-ink);
    stroke-width: 2px;
  }
  .tagline {
    font-family: "Quicksand", sans-serif;
    font-weight: 700;
    font-size: 31px;
    fill: var(--tagline-ink);
    stroke: var(--tagline-glow);
    stroke-width: 2px;
    paint-order: stroke;
  }
  .event-time {
    font-family: "Titan One", sans-serif;
    fill: var(--time-ink);
    stroke: var(--time-edge);
    stroke-width: 3px;
    paint-order: stroke;
  }
  .ticket-note {
    font-family: "Open Sans", sans-serif;
    font-style: italic;
    font-weight: 700;
    font-size: 32px;
    fill: var(--ticket-ink);
  }
</style>
</head>
<body>
<main class="poster">
  <svg width="847" height="1200" viewBox="0 0 847 1200" xmlns="http://www.w3.org/2000/svg">
    <defs>
      <linearGradient id="woodTone" x1="0" y1="0" x2="1" y2="0">
        <stop offset="0" stop-color="var(--wood-dark)"/>
        <stop offset="0.45" stop-color="var(--wood-light)"/>
        <stop offset="1" stop-color="var(--wood-mid)"/>
      </linearGradient>
      <linearGradient id="cornerLeaves" x1="0" y1="0" x2="1" y2="1">
        <stop offset="0" stop-color="var(--leaf-gold)"/>
        <stop offset="0.6" stop-color="var(--leaf-orange)"/>
        <stop offset="1" stop-color="var(--leaf-rust)"/>
      </linearGradient>
      <linearGradient id="groundLeaves" x1="0" y1="0" x2="1" y2="1">
        <stop offset="0" stop-color="var(--leaf-orange)"/>
        <stop offset="0.5" stop-color="var(--leaf-gold)"/>
        <stop offset="1" stop-color="var(--leaf-red)"/>
      </linearGradient>
    </defs>

    <rect class="wood-backdrop" x="0" y="0" width="847" height="1200" fill="url(#woodTone)" role="img" aria-label="Rustic wooden plank background with faint scattered maple leaves"/>

    <path class="leaf-cluster leaf-cluster--corner" d="M575 0 H847 V470 C820 430 760 400 740 330 C700 280 690 200 660 160 C630 120 600 60 575 0 Z" fill="url(#cornerLeaves)" role="img" aria-label="Cluster of golden and orange autumn leaves"/>

    <path class="leaf-cluster leaf-cluster--ground" d="M0 740 C60 760 120 800 180 860 C260 830 330 880 380 900 C440 870 520 890 580 860 C640 840 700 880 760 860 C800 850 830 870 847 880 V1200 H0 Z" fill="url(#groundLeaves)" role="img" aria-label="Bed of red, orange and yellow fallen leaves with a sprig of red berries"/>

    <text class="date-line" x="68" y="112" font-size="49" textLength="442" lengthAdjust="spacingAndGlyphs">SATURDAY, OCTOBER</text>
    <text class="date-line" x="160" y="175" font-size="58" textLength="258" lengthAdjust="spacingAndGlyphs">19TH 2019</text>

    <g class="title-block">
      <path class="title-frame" d="M544 200 H120 V480 H728 V200 H676"/>
      <rect class="title-leaf" x="566" y="180" width="80" height="64" rx="20" fill="#fbf3e4" role="img" aria-label="White maple leaf accent"/>
      <text class="title-word" x="139" y="356" font-size="126" textLength="541" lengthAdjust="spacingAndGlyphs">HARVEST</text>
      <text class="title-word" x="154" y="452" font-size="120" textLength="560" lengthAdjust="spacingAndGlyphs">FESTIVAL</text>
    </g>

    <text class="tagline" x="425" y="548" text-anchor="middle" textLength="638" lengthAdjust="spacingAndGlyphs">Copper Kettle Maple Lane Meadow</text>
    <text class="tagline" x="425" y="596" text-anchor="middle">Where City and Country Meet</text>
    <text class="tagline" x="425" y="675" text-anchor="middle" textLength="610" lengthAdjust="spacingAndGlyphs">Celebrate C&amp;C With Great Food,</text>
    <text class="tagline" x="425" y="725" text-anchor="middle" textLength="592" lengthAdjust="spacingAndGlyphs">Music, Entertainment, And Fun!</text>

    <text class="event-time" x="447" y="813" font-size="52" textLength="327" lengthAdjust="spacingAndGlyphs">12:00-4:00</text>
    <text class="event-time" x="567" y="871" font-size="52" textLength="87" lengthAdjust="spacingAndGlyphs">PM</text>

    <g class="ticket-note">
      <text x="57" y="994">Tickets will be</text>
      <text x="57" y="1046">available for</text>
      <text x="57" y="1096">sale at Drop off</text>
      <text x="57" y="1146">and Pick up</text>
    </g>
  </svg>
</main>
</body>
</html>
```